Business Card for Multi-Brand Sportswear Company

We are looking for a business card which represents our company and the multiple brands within it.

The company: Fen Athletics (LTD)
The brands: Fen, TavaPuni, ElmStretch, Grit and Rain

Employees using these cards would be representing Fen Athletics, rather than any of the individual brands. You will see a current design within the uploaded files, to give some inspiration. The actual text of the brands is not necessary, but the logos should be on there is some format.

Our creative minds on this are stretched, so we are looking for someone to make this their own, and show us what a good business card should look like.

We may like to get these printed with spot gloss, so keep that in mind with your designs.

www.fenathletics.co.uk

Industry/Entity Type

Business

Contact Information for Business Card

Leo Pemberton-Hale
Operations Manager
(+44) 1632 960 418
Leo@fenathletics.co.uk
www.fenathletics.co.uk

Font styles to use
Sans Serif
Other font styles liked:
• Eurostile

Colors
ffffff

Requirements
Nice to have
• Dark (black) background

```html
<!DOCTYPE html>
<html lang="en">
<head>
<meta charset="utf-8">
<title>Fen Athletics — Business Card</title>
<link rel="stylesheet" href="https://fonts.googleapis.com/css2?family=Michroma&family=Saira:wght@400;500;600&display=swap">
<style>
  :root {
    --canvas: #2b2b2d;
    --card: #0b0b0c;
    --card-edge: #161618;
    --white: #ffffff;
    --silver: #b9babd;
    --grey: #8a8b8f;
    --red: #e3222b;
    --badge-violet: #5e5470;
    --badge-coral: #e8503a;
  }
  * { margin: 0; padding: 0; box-sizing: border-box; }
  html, body {
    width: 1200px; height: 900px; overflow: hidden;
    background: var(--canvas);
  }
  .canvas {
    position: relative; width: 1200px; height: 900px;
    display: flex; flex-direction: column; align-items: center; justify-content: center; gap: 40px;
  }
  .card {
    position: relative; width: 700px; height: 400px;
    border-radius: 22px; overflow: hidden;
    background: radial-gradient(ellipse at 40% 40%, var(--card-edge), var(--card) 70%);
    box-shadow: 0 12px 30px rgba(0,0,0,.45);
  }

  /* Front */
  .front-texture {
    position: absolute; inset: 0;
    background: linear-gradient(160deg, #151517 0%, #0a0a0b 100%);
  }
  .wordmark {
    position: absolute; left: 150px; top: 118px;
    display: flex; align-items: center; gap: 18px;
  }
  .wordmark-dot {
    width: 22px; height: 22px; border-radius: 50%;
    background: var(--red);
  }
  .wordmark-name {
    font-family: "Michroma", sans-serif;
    font-size: 44px; color: var(--silver); letter-spacing: 1px;
    line-height: 1;
  }
  .tagline {
    position: absolute; left: 190px; top: 186px;
    font-family: "Saira", sans-serif; font-weight: 500;
    font-size: 15px; letter-spacing: 4px; color: var(--grey);
    text-transform: uppercase;
  }
  .brand-row {
    position: absolute; left: 0; right: 0; top: 282px;
    display: flex; justify-content: center; gap: 30px; align-items: center;
  }
  .brand-badge { width: 44px; height: 36px; }
  .brand-badge.square { background: var(--badge-violet); border-radius: 5px; }
  .brand-badge.round { width: 38px; height: 38px; border-radius: 50%; border: 3px solid var(--badge-coral); }
  .brand-badge.block { width: 38px; height: 38px; border-radius: 6px; background: var(--red); }

  /* Back */
  .accent-band {
    position: absolute; right: 0; top: 0;
    width: 26px; height: 150px;
    background: var(--red);
    border-bottom-left-radius: 14px;
  }
  .contact {
    position: absolute; right: 60px; top: 40px;
    text-align: right;
    font-family: "Saira", sans-serif; color: var(--white);
  }
  .contact-name {
    font-family: "Michroma", sans-serif; font-size: 21px; letter-spacing: .5px;
  }
  .contact-role { color: var(--red); font-size: 19px; margin-top: 2px; }
  .contact-address { font-size: 19px; line-height: 1.3; margin-top: 2px; }
  .contact-lines { margin-top: 18px; font-size: 19px; line-height: 1.3; }
  .contact-line { display: flex; justify-content: flex-end; align-items: center; gap: 10px; }
  .contact-icon { width: 16px; height: 16px; flex: none; }
  .contact-line .web-accent { color: var(--red); }
  .monogram {
    position: absolute; left: 40px; bottom: 40px;
    font-family: "Michroma", sans-serif; font-size: 110px; line-height: 1;
    color: var(--silver);
    transform-origin: left bottom;
    transform: rotate(-90deg) translate(0, 110px);
  }
</style>
</head>
<body>
<main class="canvas">

  <section class="card card-front" aria-label="Card front">
    <div class="front-texture" role="img" aria-label="Fine dark carbon-weave texture"></div>
    <div class="wordmark">
      <span class="wordmark-dot"></span>
      <span class="wordmark-name">Fen Athletics</span>
    </div>
    <p class="tagline">Performance Wear</p>
    <div class="brand-row" aria-label="Group brands">
      <span class="brand-badge square" role="img" aria-label="TavaPuni brand mark"></span>
      <span class="brand-badge block" role="img" aria-label="Grit and Rain brand mark"></span>
      <span class="brand-badge round" role="img" aria-label="ElmStretch brand mark"></span>
    </div>
  </section>

  <section class="card card-back" aria-label="Card back">
    <div class="accent-band"></div>
    <div class="contact">
      <p class="contact-name">Leo Pemberton-Hale</p>
      <p class="contact-role">Operations Manager</p>
      <p class="contact-address">Low Meadow, Carlby<br>Stamford, PE9 4TQ</p>
      <div class="contact-lines">
        <p class="contact-line">(+44) 1632 960 418
          <svg class="contact-icon" viewBox="0 0 16 16"><circle cx="8" cy="8" r="8" fill="#e3222b"/><path d="M5 4.5l1.5-.5 1 2-1 .8a5 5 0 0 0 2.2 2.2l.8-1 2 1-.5 1.5c-3 .3-6.3-3-6-6z" fill="#fff"/></svg>
        </p>
        <p class="contact-line">Leo@fenathletics.co.uk
          <svg class="contact-icon" viewBox="0 0 16 16"><circle cx="8" cy="8" r="8" fill="#e3222b"/><rect x="4" y="5" width="8" height="6" rx="1" fill="none" stroke="#fff" stroke-width="1.2"/><path d="M4 5.5l4 3 4-3" fill="none" stroke="#fff" stroke-width="1.2"/></svg>
        </p>
        <p class="contact-line">www.<span class="web-accent">fenathletics</span>.co.uk
          <svg class="contact-icon" viewBox="0 0 16 16"><circle cx="8" cy="8" r="8" fill="#e3222b"/><circle cx="8" cy="8" r="4" fill="none" stroke="#fff" stroke-width="1.2"/><path d="M4 8h8M8 4v8" stroke="#fff" stroke-width="1"/></svg>
        </p>
      </div>
    </div>
    <p class="monogram">Fen</p>
  </section>

</main>
</body>
</html>
```